Antiseptic products for Verolin East Africa

I need several antiseptic product designs for topical solutions such as surgical spirit, methylated spirit, hand sanitizer, calamine lotion, povidone solution, glycerine, povidone mouthwash, chlorhexidine solution, and sodium hypochlorite solution.

KINDLY START WITH THE HAND SANITIZER DESIGN, URGENT.

Target Market(s)

International market

Industry/Entity Type

Pharmaceutical

Font styles to use
Serif
Script

Colors
33a6d7
3277b5
0758a5
7651a1
886aae
e34197
e667a6
f78f20

Requirements
Must have
• Elegant designs, writtings to appear as they are. safety symbols to appear such as flammable or corrosive.
Nice to have
• Attractive colours but keep it simple and classy.

```html
<!DOCTYPE html>
<html lang="en">
<head>
<meta charset="utf-8">
<title>Clarivo Advanced Hand Sanitizer – Label</title>
<link rel="stylesheet" href="https://fonts.googleapis.com/css2?family=Montserrat:wght@500;600;700;800&display=swap">
<style>
  :root {
    --page-bg: #eceff3;
    --label-top: #f3f8ff;
    --label-bottom: #b8dafa;
    --ink-blue: #1f5fa6;
    --bright-blue: #2a8fd6;
    --pale-band: #cfe7fc;
    --lemon: #e9cf3a;
    --splash: #a9d6f5;
    --hazard-red: #d9262b;
    --hazard-ink: #1b1b1b;
  }
  * { margin: 0; padding: 0; box-sizing: border-box; }
  html, body {
    width: 1200px; height: 1200px; overflow: hidden;
    background: var(--page-bg);
    font-family: "Montserrat", sans-serif;
  }
  .label {
    position: absolute; left: 275px; top: 50px;
    width: 650px; height: 1100px;
    border-radius: 26px;
    background: linear-gradient(180deg, var(--label-top) 0%, #dcecfd 55%, var(--label-bottom) 100%);
    box-shadow: 0 4px 18px rgba(40, 70, 110, 0.12);
  }
  .claim-badge { position: absolute; left: 40px; top: 50px; width: 190px; height: 190px; }
  .brand-drop { position: absolute; left: 470px; top: 50px; width: 150px; height: 190px; }
  .brand-drop .drop-name {
    position: absolute; left: 0; right: 0; top: 112px;
    text-align: center; font-size: 19px; font-weight: 600;
    color: var(--ink-blue); letter-spacing: 1px;
  }
  .product-name {
    position: absolute; left: 0; right: 0; top: 330px;
    text-align: center; font-size: 104px; font-weight: 700;
    color: var(--ink-blue); letter-spacing: 1px; line-height: 1.2;
  }
  .product-type {
    position: absolute; left: 0; right: 0; top: 575px; text-align: center;
    color: var(--ink-blue);
  }
  .product-type .line-advanced { font-size: 58px; font-weight: 800; letter-spacing: 4px; line-height: 1; }
  .product-type .line-hand { font-size: 34px; font-weight: 700; letter-spacing: 3px; line-height: 1.15; margin-top: 6px; }
  .product-type .line-moist {
    display: inline-block; margin-top: 2px; padding: 2px 60px;
    font-size: 22px; font-weight: 600; letter-spacing: 2px;
    background: linear-gradient(90deg, transparent, var(--pale-band) 20%, var(--pale-band) 80%, transparent);
  }
  .product-type .line-moist strong { font-weight: 800; color: var(--bright-blue); }
  .citrus-art {
    position: absolute; left: 110px; top: 775px; width: 500px; height: 200px;
    border-radius: 50% 40% 50% 45%;
    background: radial-gradient(ellipse at 38% 55%, var(--lemon) 0%, #f1e08a 32%, var(--splash) 62%, rgba(169, 214, 245, 0) 78%);
  }
  .hazard-flammable { position: absolute; left: 36px; top: 985px; width: 84px; height: 84px; }
  .volume {
    position: absolute; right: 48px; bottom: 40px;
    color: var(--ink-blue); font-weight: 600; text-align: left;
  }
  .volume .amount { font-size: 48px; line-height: 1; display: block; }
  .volume .unit { font-size: 24px; margin-left: 44px; }
</style>
</head>
<body>
  <main class="label">
    <svg class="claim-badge" viewBox="0 0 190 190" aria-label="Kills 99% of Germs">
      <defs>
        <path id="badge-arc" d="M 13 82 A 82 82 0 0 0 177 82" />
      </defs>
      <circle cx="95" cy="82" r="60" fill="none" stroke="#2a8fd6" stroke-width="9"/>
      <circle cx="95" cy="82" r="42" fill="#cfe7fc" role="img" aria-label="Caring hands symbol"/>
      <text font-family="Montserrat, sans-serif" font-size="18" font-weight="600" fill="#1f5fa6">
        <textPath href="#badge-arc" startOffset="50%" text-anchor="middle">Kills 99% of Germs</textPath>
      </text>
    </svg>

    <div class="brand-drop">
      <svg viewBox="0 0 150 190" width="150" height="190" aria-hidden="true">
        <defs>
          <linearGradient id="drop-fill" x1="0" y1="0" x2="0" y2="1">
            <stop offset="0" stop-color="#e6f4ff"/>
            <stop offset="1" stop-color="#7cc3ec"/>
          </linearGradient>
        </defs>
        <path d="M75 6 C 92 50 140 90 140 125 A 65 62 0 0 1 10 125 C 10 90 58 50 75 6 Z" fill="url(#drop-fill)"/>
      </svg>
      <span class="drop-name">VEROLIN</span>
    </div>

    <h1 class="product-name">Clarivo</h1>

    <div class="product-type">
      <div class="line-advanced">ADVANCED</div>
      <div class="line-hand">Hand Sanitizer</div>
      <div class="line-moist">With <strong>MOISTURIZERS</strong></div>
    </div>

    <div class="citrus-art" role="img" aria-label="Lemon wedge in a water splash"></div>

    <svg class="hazard-flammable" viewBox="0 0 100 100" role="img" aria-label="Flammable">
      <rect x="17" y="17" width="66" height="66" transform="rotate(45 50 50)" fill="#ffffff" stroke="#d9262b" stroke-width="7"/>
      <path d="M50 22 C 58 34 66 40 64 54 C 63 63 57 68 50 68 C 42 68 36 62 36 54 C 36 46 42 42 44 34 C 47 40 48 44 51 46 C 53 38 52 30 50 22 Z" fill="#1b1b1b"/>
      <rect x="34" y="71" width="32" height="5" fill="#1b1b1b"/>
    </svg>

    <div class="volume">
      <span class="amount">400</span>
      <span class="unit">ml e</span>
    </div>
  </main>
</body>
</html>
```